We need a new business card that reflects who we are. Professional, classy, modern, and service ori

We need a business card design for a window coverings design company in Kansas City called Bright Lane Interiors. We offer professional, modern, and high quality window covering products. We are looking to portray an image of a big, national franchise. We are a 5 location (with showrooms) business with 10 professional designers and 4 professional installers. These cards will be used with Thank you cards, given to realtors, and asked for referrals with.

Target Market(s)

Kansas City

Industry/Entity Type

Business

Contact Information for Business Card

We would like our card to look clean and simple on the front, featuring our logo and Marlow Fenwick's. Our designers' phone numbers and emails should be displayed as well as their title.

Font styles to use
Sans Serif

Colors

Designer to choose colors to be used in the design.

Requirements
Must have
• Front - Logos, name, phone number, email address
• Back - Showroom locations, social media? Appt date/time?
Nice to have
• I would like a clean and modern look (not contemporary. I like a white background, but I am open to ideas. Looking for a "National chain" look for a small business.
Should not have
• Too much busyness.

```html
<!DOCTYPE html>
<html lang="en">
<head>
<meta charset="utf-8">
<title>Bright Lane Interiors – Business Card</title>
<link rel="stylesheet" href="https://fonts.googleapis.com/css2?family=Roboto:wght@400;500;700&family=Roboto+Condensed:wght@500&display=swap">
<style>
  :root {
    --backdrop: #2b2b2b;
    --card: #f4f4f4;
    --card-top: #a9abad;
    --red: #c7373c;
    --ink: #1c1c1c;
    --grey-text: #555759;
    --grey-list: #5a5c5e;
    --partner-orange: #f0951f;
    --partner-text: #5e6b78;
    --rule: #8a8a8a;
  }
  * { box-sizing: border-box; margin: 0; padding: 0; }
  html, body { width: 1200px; height: 960px; overflow: hidden; }
  body {
    background: var(--backdrop);
    position: relative;
    font-family: "Roboto", Arial, sans-serif;
  }
  .card {
    position: absolute;
    width: 600px;
    height: 343px;
    background: var(--card);
  }
  .card--front {
    left: 314px; top: 113px;
    background: linear-gradient(to bottom, var(--card-top) 0%, #d9dadb 30%, #eeeeee 52%, var(--card) 72%);
  }
  .card--back { left: 311px; top: 472px; }

  /* Front */
  .designer {
    position: absolute; right: 42px; top: 42px; text-align: right;
  }
  .designer__name {
    font-family: "Roboto Condensed", "Arial Narrow", sans-serif;
    font-weight: 500; font-size: 25px; color: var(--red); letter-spacing: 0.3px;
    line-height: 28px;
  }
  .designer__title {
    font-weight: 500; font-size: 15px; color: var(--ink); line-height: 20px; letter-spacing: 0.3px;
  }
  .designer__phone {
    margin-top: 4px; font-size: 14px; color: var(--grey-text);
    display: flex; justify-content: flex-end; align-items: center; gap: 6px;
  }
  .designer__phone svg { width: 13px; height: 13px; }
  .web-contact {
    position: absolute; left: 42px; top: 273px;
    font-size: 14.5px; color: var(--grey-text); line-height: 19px;
  }

  .brand { position: absolute; text-align: center; }
  .brand__row { display: flex; align-items: center; justify-content: center; gap: 8px; }
  .brand__mark { width: 14px; height: 14px; background: var(--red); }
  .brand__name { font-weight: 500; font-size: 22px; color: var(--ink); letter-spacing: 0.2px; }
  .brand__tagline { margin-top: 4px; font-size: 11.5px; color: var(--ink); }
  .card--front .brand { left: 322px; top: 264px; width: 240px; }
  .card--back .brand { left: 50px; top: 134px; width: 230px; }

  /* Back */
  .showrooms {
    position: absolute; right: 53px; top: 44px; text-align: right;
    font-weight: 500; font-size: 14.5px; line-height: 18px; color: var(--grey-list);
    list-style: none;
  }
  .showrooms__heading { color: var(--red); font-weight: 700; }
  .partner {
    position: absolute; right: 53px; top: 156px;
    display: flex; align-items: center; gap: 4px;
    font-size: 12.5px; font-weight: 700; color: var(--partner-text);
  }
  .partner__dot { width: 16px; height: 16px; border-radius: 50%; background: var(--partner-orange); }
  .social {
    position: absolute; right: 53px; top: 184px; display: flex; gap: 2px;
  }
  .social span { width: 18px; height: 18px; border-radius: 50%; background: var(--red); }

  .appointment { position: absolute; left: 52px; right: 50px; color: var(--red); font-size: 16px; }
  .appointment__row { display: flex; align-items: baseline; }
  .appointment__label { white-space: nowrap; margin-right: 4px; }
  .appointment__line { flex: 1; border-bottom: 1px dotted var(--rule); height: 1px; }
  .appointment__line--short { flex: 0 0 140px; }
  .appointment__unit { font-size: 12px; margin-left: 6px; }
  .appointment__gap { width: 4px; }
  .appointment--name { top: 237px; }
  .appointment--time { top: 278px; }
</style>
</head>
<body>

<section class="card card--front" aria-label="Card front">
  <div class="designer">
    <p class="designer__name">EVAN CARTER</p>
    <p class="designer__title">DESIGNER</p>
    <p class="designer__phone">913.555.0147
      <svg viewBox="0 0 24 24" aria-hidden="true"><path fill="#c7373c" d="M6.6 10.8a15.1 15.1 0 0 0 6.6 6.6l2.2-2.2c.3-.3.7-.4 1-.2 1.1.4 2.3.6 3.6.6.6 0 1 .4 1 1V20c0 .6-.4 1-1 1C10.6 21 3 13.4 3 4c0-.6.4-1 1-1h3.5c.6 0 1 .4 1 1 0 1.3.2 2.5.6 3.6.1.3 0 .7-.2 1z"/></svg>
    </p>
  </div>

  <div class="web-contact">
    <p>info@brightlaneinteriors.com</p>
    <p>www.brightlaneinteriors.com</p>
  </div>

  <div class="brand">
    <div class="brand__row"><span class="brand__mark"></span><span class="brand__name">Bright Lane Interiors</span></div>
    <p class="brand__tagline">Blinds, Shades, Shutters, Draperies &amp; Decor</p>
  </div>
</section>

<section class="card card--back" aria-label="Card back">
  <div class="brand">
    <div class="brand__row"><span class="brand__mark"></span><span class="brand__name">Bright Lane Interiors</span></div>
    <p class="brand__tagline">Blinds, Shades, Shutters, Draperies &amp; Decor</p>
  </div>

  <ul class="showrooms">
    <li class="showrooms__heading">SHOWROOM LOCATIONS</li>
    <li>ASHBURY</li>
    <li>CEDAR HOLLOW</li>
    <li>MAPLE RIDGE</li>
    <li>BROOKFIELD</li>
    <li>FAIRHAVEN</li>
  </ul>

  <div class="partner"><span>Marlow Fenwick</span><span class="partner__dot"></span></div>

  <div class="social" aria-label="Social media">
    <span></span><span></span><span></span><span></span>
  </div>

  <div class="appointment appointment--name">
    <div class="appointment__row"><span class="appointment__label">Name :</span><span class="appointment__line"></span></div>
  </div>
  <div class="appointment appointment--time">
    <div class="appointment__row">
      <span class="appointment__label">Date :</span><span class="appointment__line"></span>
      <span class="appointment__gap"></span>
      <span class="appointment__label">Time :</span><span class="appointment__line appointment__line--short"></span>
      <span class="appointment__unit">AM/PM</span>
    </div>
  </div>
</section>

</body>
</html>
```